Bran-well Tide Gate Custom Brokers Limited

Name: Lorvina Hadcott
Title: Customs Broker
Address: Shop 9 Ferncliff Commercial Complex
207-209 Mulgrave Road
Kingston 8
Telephone: (876)
Email: tidegatewell@mailbrook.example

```html
<!DOCTYPE html>
<html lang="en">
<head>
<meta charset="utf-8">
<title>Bran-well Tide Gate Custom Brokers Limited – Business Card</title>
<link href="https://fonts.googleapis.com/css2?family=Montserrat:wght@800&family=Poppins:wght@400;500;600&display=swap" rel="stylesheet">
<style>
  :root {
    --navy: #0d2b55;
    --gold: #eaaa0b;
    --white: #ffffff;
    --grey: #9a9fa8;
    --backdrop: #2a2a2a;
  }
  * { box-sizing: border-box; margin: 0; padding: 0; }
  html, body {
    width: 1200px; height: 1200px; overflow: hidden;
    background: var(--backdrop);
    font-family: "Poppins", sans-serif;
  }
  .sheet {
    position: relative; width: 1200px; height: 1200px;
  }
  .card {
    position: absolute; left: 120px; width: 960px; height: 540px;
    background: var(--white); overflow: hidden;
    box-shadow: 0 12px 30px rgba(0,0,0,.45);
  }
  .card--front { top: 30px; }
  .card--back { top: 630px; }
  .card__art { position: absolute; inset: 0; width: 100%; height: 100%; }

  .brand {
    position: absolute; display: flex; align-items: center; gap: 18px;
    color: var(--navy); font-weight: 600;
  }
  .brand__dot {
    width: 46px; height: 46px; border-radius: 50%; background: var(--gold); flex: none;
  }
  .brand__text { line-height: 1.1; }
  .brand__name { font-size: 40px; letter-spacing: 1px; text-transform: uppercase; }
  .brand__tag { font-size: 20px; letter-spacing: 7px; }
  .card--front .brand { left: 200px; top: 190px; }
  .card--back .brand { right: 60px; top: 150px; }
  .card--back .brand__name { font-size: 34px; }
  .card--back .brand__tag { font-size: 17px; letter-spacing: 6px; }

  .person { position: absolute; left: 70px; top: 200px; }
  .person__name {
    font-family: "Montserrat", sans-serif; font-weight: 800;
    font-size: 34px; color: var(--navy); text-transform: uppercase; letter-spacing: .5px;
  }
  .person__role { font-size: 22px; color: var(--gold); margin-top: 2px; }

  .contact { position: absolute; left: 60px; top: 340px; list-style: none; }
  .contact__item {
    display: flex; align-items: center; gap: 14px;
    font-size: 22px; color: var(--navy); line-height: 1.7;
  }
  .contact__icon {
    width: 26px; height: 26px; border-radius: 50%; background: var(--gold);
    display: flex; align-items: center; justify-content: center; flex: none;
  }

  .address {
    position: absolute; right: 60px; top: 300px; text-align: right;
    font-style: normal; font-size: 21px; font-weight: 500; color: var(--navy); line-height: 1.45;
  }
</style>
</head>
<body>
<main class="sheet">

  <section class="card card--front" aria-label="Card front">
    <svg class="card__art" viewBox="0 0 960 540" preserveAspectRatio="none" aria-hidden="true">
      <path d="M0,405 Q500,500 960,478 L960,540 L0,540Z" fill="var(--gold)"/>
      <path d="M0,420 Q500,515 960,492 L960,540 L0,540Z" fill="var(--navy)"/>
    </svg>
    <div class="brand">
      <span class="brand__dot"></span>
      <div class="brand__text">
        <div class="brand__name">Bran-well Tide Gate</div>
        <div class="brand__tag">Custom Brokers Ltd.</div>
      </div>
    </div>
  </section>

  <section class="card card--back" aria-label="Card back">
    <svg class="card__art" viewBox="0 0 960 540" preserveAspectRatio="none" aria-hidden="true">
      <path d="M0,0 L600,0 Q230,30 0,175Z" fill="var(--navy)"/>
      <path d="M0,70 Q150,18 380,0" fill="none" stroke="var(--gold)" stroke-width="9"/>
      <path d="M0,110 Q180,35 470,6" fill="none" stroke="var(--white)" stroke-width="24"/>
      <path d="M0,440 Q500,520 960,498 L960,540 L0,540Z" fill="var(--gold)"/>
      <path d="M0,455 Q500,530 960,510 L960,540 L0,540Z" fill="var(--navy)"/>
    </svg>

    <div class="person">
      <h1 class="person__name">Lorvina Hadcott</h1>
      <p class="person__role">Customs Broker</p>
    </div>

    <ul class="contact">
      <li class="contact__item">
        <span class="contact__icon">
          <svg width="14" height="14" viewBox="0 0 14 14" aria-hidden="true"><rect x="3" y="1" width="8" height="12" rx="1.5" fill="none" stroke="#fff" stroke-width="1.6"/></svg>
        </span>
        (876) 555 019 4420
      </li>
      <li class="contact__item">
        <span class="contact__icon">
          <svg width="14" height="14" viewBox="0 0 14 14" aria-hidden="true"><rect x="1" y="3" width="12" height="8" fill="none" stroke="#fff" stroke-width="1.5"/><path d="M1,3 L7,8 L13,3" fill="none" stroke="#fff" stroke-width="1.5"/></svg>
        </span>
        tidegatewell@mailbrook.example
      </li>
    </ul>

    <div class="brand">
      <span class="brand__dot"></span>
      <div class="brand__text">
        <div class="brand__name">Bran-well Tide Gate</div>
        <div class="brand__tag">Custom Brokers Ltd.</div>
      </div>
    </div>

    <address class="address">
      Shop 9 Ferncliff Commercial Complex<br>
      207-209 Mulgrave Road<br>
      Kingston 8
    </address>
  </section>

</main>
</body>
</html>
```